Call Center In Need of Website Design

We are a call center that provides inbound and outbound calling & marketing services for eCommerce store. We would like to see a fun, creative, playful design that is simple.

Here are some sample design sites we like;
- https://www.velmoreline.com/
- https://pindrask.io/
- https://www.glimbertic.com/live-chat-software/
- https://www.zavrolin.com/

Here are some competitor sites;
- https://www.ostrevaglinks.com/
- https://www.helpkestrel.com/

I have attached website content for your use.

Target Market(s)

eCommerce

Coding

Coded - Design and coding required

Number of Pages Required

5+ page

Font styles to use
Sans Serif

Colors

Designer to choose colors to be used in the design.

Requirements
Must have
• Must have designs for the following 5 separate pages;
• 1. Home (landing)
• - This will be were the design style really needs to show.
• - Just needs to touch on key services
• - CTA
• 2. About Us
• - Basic page for about me paragraph
• 3. Services
• - List of services with icons
• - Click on service type to expand details or hover over service icon to view popup bubble with details about that service
• 4. Pricing
• - Option to bundle 1(one) digital service plan and 1(one) call center service plan
• - Bundling adds 10% monthly discount to over all price
• - Customer does NOT have to bundle
• - FAQ
• 5. Contact Us
• - Include a capture form (name, company name, email, phone, message)
• - Contact info
• - Business hours
• When customer purchases their desired plan, then they are taken to a page where they must schedule a call with an account rep.
Nice to have
• home page animations
Should not have
• All information on Home/Landing page.

```html
<!DOCTYPE html>
<html lang="en">
<head>
<meta charset="utf-8">
<title>Loftwell — Pricing</title>
<link href="https://fonts.googleapis.com/css2?family=Archivo+Black&family=Open+Sans:wght@400;600;700&display=swap" rel="stylesheet">
<style>
:root{
  --purple:#38368c;
  --purple-deep:#2c2a78;
  --navy:#2b2a86;
  --mint:#6dcfb2;
  --mint-soft:#8fdcc5;
  --white:#ffffff;
  --ink:#2a2a3a;
  --grey:#8a8a95;
  --line-light:#c9c9d6;
}
*{box-sizing:border-box;margin:0;padding:0}
html,body{width:1200px;height:4444px;overflow:hidden}
body{position:relative;font-family:"Open Sans",Arial,sans-serif;background:var(--white);color:var(--ink)}
.band{position:absolute;left:0;width:1200px}
.abs{position:absolute}
.connectors{position:absolute;left:0;top:0;width:1200px;pointer-events:none}

/* header */
.hero{top:0;height:440px;background:var(--purple);overflow:hidden}
.brand{left:48px;top:22px;display:flex;align-items:center;gap:14px;color:var(--white);font-family:"Open Sans",sans-serif;font-weight:600;font-size:34px;letter-spacing:6px}
.brand-dot{width:40px;height:40px;border-radius:50%;border:3px solid var(--mint)}
.main-nav{left:556px;top:40px;display:flex;gap:34px}
.main-nav a{color:var(--white);font-size:11px;font-weight:600;text-decoration:none;letter-spacing:.5px;padding-bottom:6px}
.main-nav a.active{border-bottom:2px solid var(--mint)}
.hero-title{left:160px;top:145px;font-family:"Archivo Black",Arial,sans-serif;color:var(--white);font-size:54px;line-height:72px}
.hero-sub{left:162px;top:296px;color:var(--white);font-size:16px;letter-spacing:5px;font-weight:600}
.art{background:linear-gradient(160deg,#5553a8,#46449a)}
.hero-cloud{left:0;top:330px;width:1200px;height:110px}

/* pricing sections */
.mint{background:var(--mint)}
.violet{background:var(--purple)}
.plain{background:var(--white)}
.sec-title{left:0;width:1200px;text-align:center;font-family:"Archivo Black",Arial,sans-serif;font-size:24px;color:var(--white)}
.plan-title{left:0;width:1200px;text-align:center;font-family:"Archivo Black",Arial,sans-serif;font-size:15px;text-decoration:underline;text-underline-offset:4px}
.mint .plan-title{color:var(--navy)}
.plain .plan-title{color:var(--ink)}
.violet .plan-title{color:var(--white)}
.plan-box{position:absolute;width:133px;height:95px;display:flex;flex-direction:column;align-items:center;justify-content:center;gap:8px;text-align:center;font-size:11px;font-weight:700;line-height:14px;padding:0 8px}
.plan-box.dark{background:var(--purple);color:var(--white);border:1px solid rgba(255,255,255,.35)}
.plan-box.light{background:var(--white);color:var(--ink);height:90px;box-shadow:0 2px 6px rgba(0,0,0,.12)}
.plan-box.wide{width:207px}
.ico{width:30px;height:30px}
.dark .ico{color:var(--white)}
.light .ico{color:var(--navy)}

/* faq */
.faq-title{left:0;width:1200px;top:80px;text-align:center;font-family:"Archivo Black",Arial,sans-serif;font-size:26px;color:var(--navy)}
.faq-rule{left:570px;top:122px;width:60px;height:3px;background:var(--mint)}
.faq-item{position:absolute;width:421px;height:34px;background:#f3f3f6;display:flex;align-items:center;justify-content:space-between;padding:0 14px;font-size:11px;font-weight:600;color:var(--ink)}
.faq-item b{font-size:18px;font-weight:700}
.faq-item.open{background:var(--mint);color:var(--white)}
.faq-answer{position:absolute;width:421px;background:var(--mint-soft);color:var(--white);font-size:10px;line-height:15px;padding:8px 14px}
.cta-text{left:0;width:1200px;top:548px;text-align:center;font-family:"Archivo Black",Arial,sans-serif;font-size:40px;line-height:58px;color:var(--navy)}
.cta-btn{left:520px;top:663px;width:160px;height:42px;border-radius:21px;background:var(--mint);color:var(--white);font-size:12px;font-weight:700;display:flex;align-items:center;justify-content:center;letter-spacing:.5px}

/* contact */
.contact-card{left:187px;top:59px;width:278px;height:228px;background:rgba(255,255,255,.22);padding:26px 24px;color:var(--white)}
.contact-card h3{font-size:15px;font-weight:700;padding-bottom:10px;border-bottom:2px solid var(--white);display:inline-block;margin-bottom:22px}
.contact-row{display:flex;gap:10px;font-size:11px;line-height:16px;margin-bottom:12px}
.contact-row svg{width:14px;height:14px;flex:none;color:var(--white)}
.form-title{left:489px;top:66px;color:var(--white);font-size:30px;font-weight:600}
.field{position:absolute;height:36px;width:252px;border:1px solid rgba(255,255,255,.8);background:rgba(255,255,255,.15);color:var(--white);font-size:11px;padding:0 12px;display:flex;align-items:center}
.submit{left:489px;top:248px;width:112px;height:34px;background:var(--purple);color:var(--white);font-size:11px;font-weight:700;display:flex;align-items:center;justify-content:center}

/* footer */
.copy{left:163px;top:44px;font-size:10px;line-height:15px;color:var(--grey)}
.foot-nav{left:410px;top:48px;display:flex;gap:26px}
.foot-nav a{font-size:11px;color:var(--grey);text-decoration:none}
.foot-nav a.active{color:var(--mint)}
.socials{left:928px;top:44px;display:flex;gap:8px}
.socials span{width:22px;height:22px;background:var(--purple)}
</style>
</head>
<body>

<svg width="0" height="0" style="position:absolute">
  <defs>
    <marker id="arrow-dark" viewBox="0 0 10 10" refX="5" refY="5" markerWidth="6" markerHeight="6" orient="auto"><path d="M0 0L10 5L0 10z" fill="#9aa0b4"/></marker>
    <marker id="arrow-light" viewBox="0 0 10 10" refX="5" refY="5" markerWidth="6" markerHeight="6" orient="auto"><path d="M0 0L10 5L0 10z" fill="#ffffff"/></marker>
    <symbol id="i-dollar" viewBox="0 0 24 24"><text x="12" y="20" text-anchor="middle" font-family="Arial" font-weight="700" font-size="22" fill="currentColor">$</text></symbol>
    <symbol id="i-mail" viewBox="0 0 24 24"><rect x="2" y="5" width="20" height="14" rx="1.5" fill="none" stroke="currentColor" stroke-width="2"/><path d="M3 6l9 7 9-7" fill="none" stroke="currentColor" stroke-width="2"/></symbol>
    <symbol id="i-chat" viewBox="0 0 24 24"><path d="M2 4h13v9H7l-4 3v-3H2z" fill="none" stroke="currentColor" stroke-width="2" stroke-linejoin="round"/><path d="M17 8h5v9h-1v3l-4-3h-6v-2" fill="none" stroke="currentColor" stroke-width="2" stroke-linejoin="round"/></symbol>
    <symbol id="i-search" viewBox="0 0 24 24"><rect x="4" y="2" width="14" height="19" fill="none" stroke="currentColor" stroke-width="2"/><circle cx="15" cy="15" r="4" fill="none" stroke="currentColor" stroke-width="2"/><path d="M18 18l4 4" stroke="currentColor" stroke-width="2"/></symbol>
    <symbol id="i-list" viewBox="0 0 24 24"><rect x="4" y="2" width="16" height="20" fill="none" stroke="currentColor" stroke-width="2"/><path d="M8 8h8M8 12h8M8 16h5" stroke="currentColor" stroke-width="2"/></symbol>
    <symbol id="i-tag" viewBox="0 0 24 24"><rect x="3" y="3" width="18" height="18" fill="none" stroke="currentColor" stroke-width="2"/><path d="M7 16l4-4 3 3 4-5" fill="none" stroke="currentColor" stroke-width="2"/></symbol>
    <symbol id="i-box" viewBox="0 0 24 24"><path d="M12 2l9 5v10l-9 5-9-5V7z" fill="none" stroke="currentColor" stroke-width="2" stroke-linejoin="round"/><path d="M3 7l9 5 9-5M12 12v10" fill="none" stroke="currentColor" stroke-width="2"/></symbol>
    <symbol id="i-clock" viewBox="0 0 24 24"><circle cx="12" cy="12" r="9" fill="none" stroke="currentColor" stroke-width="2"/><path d="M12 7v5l4 2" fill="none" stroke="currentColor" stroke-width="2"/></symbol>
    <symbol id="i-agent" viewBox="0 0 24 24"><circle cx="12" cy="8" r="5" fill="currentColor"/><path d="M3 22c0-5 4-8 9-8s9 3 9 8z" fill="currentColor"/></symbol>
    <symbol id="i-phone" viewBox="0 0 24 24"><path d="M5 3h4l2 5-3 2c1 3 3 5 6 6l2-3 5 2v4c0 1-1 2-2 2C10 21 3 14 3 5c0-1 1-2 2-2z" fill="none" stroke="currentColor" stroke-width="2" stroke-linejoin="round"/></symbol>
    <symbol id="i-chart" viewBox="0 0 24 24"><path d="M3 21h18" stroke="currentColor" stroke-width="2"/><rect x="5" y="13" width="3" height="7" fill="currentColor"/><rect x="10.5" y="9" width="3" height="11" fill="currentColor"/><rect x="16" y="5" width="3" height="15" fill="currentColor"/></symbol>
    <symbol id="i-tools" viewBox="0 0 24 24"><path d="M4 4l16 16M20 4L4 20" stroke="currentColor" stroke-width="3" stroke-linecap="round"/></symbol>
    <symbol id="i-return" viewBox="0 0 24 24"><path d="M20 12a8 8 0 1 1-3-6.2" fill="none" stroke="currentColor" stroke-width="2"/><path d="M18 2v5h-5" fill="none" stroke="currentColor" stroke-width="2"/></symbol>
    <symbol id="i-pin" viewBox="0 0 24 24"><path d="M12 22s7-7 7-12a7 7 0 0 0-14 0c0 5 7 12 7 12z" fill="currentColor"/><circle cx="12" cy="10" r="2.5" fill="#6dcfb2"/></symbol>
  </defs>
</svg>

<!-- Header -->
<header class="band hero">
  <div class="abs brand"><span class="brand-dot"></span>LOFTWELL</div>
  <nav class="abs main-nav">
    <a class="active">HOME</a><a>ABOUT US</a><a>SERVICES</a><a>PRICING</a><a>CONTACT US</a><a>ACCOUNT</a>
  </nav>
  <div class="abs art" role="img" aria-label="Small rocket illustration launching" style="left:62px;top:82px;width:34px;height:90px;border-radius:17px"></div>
  <h1 class="abs hero-title">Loftwell Is An<br>Omnichannel</h1>
  <p class="abs hero-sub">Provider For Customer Care</p>
  <div class="abs art" role="img" aria-label="Astronaut floating in space with sparkling stars" style="left:790px;top:0;width:410px;height:370px;border-radius:0 0 0 180px"></div>
  <svg class="abs hero-cloud" viewBox="0 0 1200 110" preserveAspectRatio="none" aria-hidden="true">
    <path d="M0 50 Q40 10 90 45 Q140 5 200 48 Q260 20 320 55 Q400 25 470 60 Q560 30 640 62 Q720 35 800 58 Q880 20 960 50 Q1040 15 1110 45 Q1160 20 1200 40 V110 H0Z" fill="#6dcfb2"/>
  </svg>
</header>

<!-- Digital – Standard -->
<section class="band mint" style="top:440px;height:582px">
  <svg class="connectors" height="582" aria-hidden="true" fill="none" stroke="#9aa0b4" stroke-width="1.5">
    <path d="M600 137V423" marker-end="url(#arrow-dark)"/>
    <path d="M229.5 197H972.5"/>
    <path d="M229.5 197V275M371.5 197V275M513.5 197V275M688.5 197V275M830.5 197V275M972.5 197V275" marker-end="url(#arrow-dark)"/>
  </svg>
  <h2 class="abs sec-title" style="top:50px">PRICING</h2>
  <div class="abs" style="left:585px;top:44px;width:30px;height:2px;background:#fff"></div>
  <h3 class="abs plan-title" style="top:107px">DIGITAL – STANDARD</h3>
  <div class="abs art" role="img" aria-label="Astronaut planting a flag on a small moon" style="left:18px;top:330px;width:120px;height:210px;border-radius:60px 60px 20px 20px;background:linear-gradient(180deg,#f2f4f8,#9fa8c0)"></div>
  <div class="plan-box dark" style="left:163px;top:280px"><svg class="ico"><use href="#i-dollar"/></svg>$69 Per Month</div>
  <div class="plan-box dark" style="left:305px;top:280px"><svg class="ico"><use href="#i-mail"/></svg>Unlimited Email Support</div>
  <div class="plan-box dark" style="left:447px;top:280px"><svg class="ico"><use href="#i-chat"/></svg>Unlimited Live Chat Support</div>
  <div class="plan-box dark" style="left:622px;top:280px"><svg class="ico"><use href="#i-search"/></svg>Product Research (5 per month)</div>
  <div class="plan-box dark" style="left:764px;top:280px"><svg class="ico"><use href="#i-list"/></svg>Product Listing (5 per month)</div>
  <div class="plan-box dark" style="left:906px;top:280px"><svg class="ico"><use href="#i-tag"/></svg>Price Monitoring (10 product / month)</div>
  <div class="plan-box dark wide" style="left:497px;top:428px"><svg class="ico"><use href="#i-box"/></svg>Product Photo &amp; Video Editing (5 photos &amp; 1, 10 second video)</div>
</section>

<!-- Digital – Business -->
<section class="band plain" style="top:1022px;height:548px">
  <svg class="connectors" height="548" aria-hidden="true" fill="none" stroke="#9aa0b4" stroke-width="1.5">
    <path d="M600 100V380" marker-end="url(#arrow-dark)"/>
    <path d="M229.5 154H972.5"/>
    <path d="M229.5 154V231M371.5 154V231M513.5 154V231M688.5 154V231M830.5 154V231M972.5 154V231" marker-end="url(#arrow-dark)"/>
  </svg>
  <h3 class="abs plan-title" style="top:72px">DIGITAL – BUSINESS</h3>
  <div class="plan-box dark" style="left:163px;top:237px"><svg class="ico"><use href="#i-dollar"/></svg>$199 Per Month</div>
  <div class="plan-box dark" style="left:305px;top:237px"><svg class="ico"><use href="#i-mail"/></svg>Unlimited Email Support</div>
  <div class="plan-box dark" style="left:447px;top:237px"><svg class="ico"><use href="#i-chat"/></svg>Unlimited Live Chat Support</div>
  <div class="plan-box dark" style="left:622px;top:237px"><svg class="ico"><use href="#i-search"/></svg>Product Research (30 per month)</div>
  <div class="plan-box dark" style="left:764px;top:237px"><svg class="ico"><use href="#i-list"/></svg>Product Listing (30 per month)</div>
  <div class="plan-box dark" style="left:906px;top:237px"><svg class="ico"><use href="#i-tag"/></svg>Price Monitoring (50 product / month)</div>
  <div class="plan-box dark wide" style="left:497px;top:385px"><svg class="ico"><use href="#i-box"/></svg>Product Photo &amp; Video Editing (5 photos &amp; 1, 10 second video)</div>
</section>

<!-- Call Center – Standard -->
<section class="band violet" style="top:1570px;height:839px">
  <svg class="connectors" height="839" aria-hidden="true" fill="none" stroke="#ffffff" stroke-width="1.5" stroke-dasharray="4 3">
    <path d="M600 97V593"/>
    <path d="M229.5 154H972.5M229.5 386H972.5M229.5 593H972.5"/>
    <path d="M229.5 154V231M371.5 154V231M513.5 154V231M688.5 154V231M830.5 154V231M972.5 154V231" marker-end="url(#arrow-light)"/>
    <path d="M229.5 386V424M371.5 386V424M513.5 386V424M688.5 386V424M830.5 386V424M972.5 386V424" marker-end="url(#arrow-light)"/>
    <path d="M229.5 593V631M371.5 593V631M513.5 593V631M688.5 593V631M830.5 593V631M972.5 593V631" marker-end="url(#arrow-light)"/>
  </svg>
  <h3 class="abs plan-title" style="top:68px">CALL CENTER – STANDARD</h3>
  <div class="plan-box light" style="left:163px;top:237px"><svg class="ico"><use href="#i-dollar"/></svg>$59 Per Month (7 day free trial)</div>
  <div class="plan-box light" style="left:305px;top:237px"><svg class="ico"><use href="#i-mail"/></svg>Unlimited Email Support</div>
  <div class="plan-box light" style="left:447px;top:237px"><svg class="ico"><use href="#i-clock"/></svg>$1.15 Per Minute</div>
  <div class="plan-box light" style="left:622px;top:237px"><svg class="ico"><use href="#i-agent"/></svg>Live Personalized Receptionist Service</div>
  <div class="plan-box light" style="left:764px;top:237px"><svg class="ico"><use href="#i-mail"/></svg>Text &amp; Email Delivery</div>
  <div class="plan-box light" style="left:906px;top:237px"><svg class="ico"><use href="#i-phone"/></svg>Includes Nationwide 800 Number</div>
  <div class="plan-box light" style="left:163px;top:430px"><svg class="ico"><use href="#i-agent"/></svg>Answering service</div>
  <div class="plan-box light" style="left:305px;top:430px"><svg class="ico"><use href="#i-phone"/></svg>Welcome Calls</div>
  <div class="plan-box light" style="left:447px;top:430px"><svg class="ico"><use href="#i-phone"/></svg>Follow-Up Service</div>
  <div class="plan-box light" style="left:622px;top:430px"><svg class="ico"><use href="#i-chart"/></svg>Customer Upselling</div>
  <div class="plan-box light" style="left:764px;top:430px"><svg class="ico"><use href="#i-phone"/></svg>Over-The-Phone Order Taking</div>
  <div class="plan-box light" style="left:906px;top:430px"><svg class="ico"><use href="#i-return"/></svg>Order Return Processing</div>
  <div class="plan-box light" style="left:163px;top:637px"><svg class="ico"><use href="#i-agent"/></svg>Feedback/Survey Calls</div>
  <div class="plan-box light" style="left:305px;top:637px"><svg class="ico"><use href="#i-mail"/></svg>Message Delivering Service</div>
  <div class="plan-box light" style="left:447px;top:637px"><svg class="ico"><use href="#i-chart"/></svg>ROI Diagnostics &amp; Reporting</div>
  <div class="plan-box light" style="left:622px;top:637px"><svg class="ico"><use href="#i-agent"/></svg>Scalable Call Center Pricing</div>
  <div class="plan-box light" style="left:764px;top:637px"><svg class="ico"><use href="#i-tools"/></svg>Customizable for Any Industry</div>
  <div class="plan-box light" style="left:906px;top:637px"><svg class="ico"><use href="#i-agent"/></svg>100% US-Based Agents</div>
</section>

<!-- Call Center – Standard (higher tier) -->
<section class="band mint" style="top:2409px;height:806px">
  <svg class="connectors" height="806" aria-hidden="true" fill="none" stroke="#ffffff" stroke-width="1.5" stroke-dasharray="4 3">
    <path d="M600 91V590"/>
    <path d="M229.5 154H972.5M229.5 391H972.5M229.5 590H972.5"/>
    <path d="M229.5 154V228M371.5 154V228M513.5 154V228M688.5 154V228M830.5 154V228M972.5 154V228" marker-end="url(#arrow-light)"/>
    <path d="M229.5 391V430M371.5 391V430M513.5 391V430M688.5 391V430M830.5 391V430M972.5 391V430" marker-end="url(#arrow-light)"/>
    <path d="M229.5 590V628M371.5 590V628M513.5 590V628M688.5 590V628M830.5 590V628M972.5 590V628" marker-end="url(#arrow-light)"/>
  </svg>
  <h3 class="abs plan-title" style="top:62px;color:#fff">CALL CENTER – STANDARD</h3>
  <div class="plan-box light" style="left:163px;top:234px"><svg class="ico"><use href="#i-dollar"/></svg>$249 Per Month (7 day free trial)</div>
  <div class="plan-box light" style="left:305px;top:234px"><svg class="ico"><use href="#i-mail"/></svg>Unlimited Email Support</div>
  <div class="plan-box light" style="left:447px;top:234px"><svg class="ico"><use href="#i-clock"/></svg>$1.05 Per Minute</div>
  <div class="plan-box light" style="left:622px;top:234px"><svg class="ico"><use href="#i-agent"/></svg>Live Personalized Receptionist Service</div>
  <div class="plan-box light" style="left:764px;top:234px"><svg class="ico"><use href="#i-mail"/></svg>Text &amp; Email Delivery</div>
  <div class="plan-box light" style="left:906px;top:234px"><svg class="ico"><use href="#i-phone"/></svg>Includes Nationwide 800 Number</div>
  <div class="plan-box light" style="left:163px;top:436px"><svg class="ico"><use href="#i-agent"/></svg>Answering service</div>
  <div class="plan-box light" style="left:305px;top:436px"><svg class="ico"><use href="#i-phone"/></svg>Welcome Calls</div>
  <div class="plan-box light" style="left:447px;top:436px"><svg class="ico"><use href="#i-phone"/></svg>Follow-Up Service</div>
  <div class="plan-box light" style="left:622px;top:436px"><svg class="ico"><use href="#i-chart"/></svg>Customer Upselling</div>
  <div class="plan-box light" style="left:764px;top:436px"><svg class="ico"><use href="#i-phone"/></svg>Over-The-Phone Order Taking</div>
  <div class="plan-box light" style="left:906px;top:436px"><svg class="ico"><use href="#i-return"/></svg>Order Return Processing</div>
  <div class="plan-box light" style="left:163px;top:634px"><svg class="ico"><use href="#i-agent"/></svg>Feedback/Survey Calls</div>
  <div class="plan-box light" style="left:305px;top:634px"><svg class="ico"><use href="#i-mail"/></svg>Message Delivering Service</div>
  <div class="plan-box light" style="left:447px;top:634px"><svg class="ico"><use href="#i-chart"/></svg>ROI Diagnostics &amp; Reporting</div>
  <div class="plan-box light" style="left:622px;top:634px"><svg class="ico"><use href="#i-agent"/></svg>Scalable Call Center Pricing</div>
  <div class="plan-box light" style="left:764px;top:634px"><svg class="ico"><use href="#i-tools"/></svg>Customizable for Any Industry</div>
  <div class="plan-box light" style="left:906px;top:634px"><svg class="ico"><use href="#i-agent"/></svg>100% US-Based Agents</div>
</section>

<!-- FAQ + CTA -->
<section class="band plain" style="top:3215px;height:785px">
  <h2 class="abs faq-title">Frequently Asked Questions</h2>
  <div class="abs faq-rule"></div>
  <div class="faq-item open" style="left:163px;top:157px">IS THE FREE TRIAL REALLY FREE? <b>−</b></div>
  <p class="faq-answer" style="left:163px;top:191px">The free trial applies to our call center plans only. There is no hidden fine print and no hoops to jump through. We never ask for payment details, signatures or deposits up front. If the service is not for you, simply walk away.</p>
  <div class="faq-item" style="left:163px;top:257px">Do you offer custom script writing? <b>+</b></div>
  <div class="faq-item" style="left:163px;top:299px">Why do you use time-based billing over standard billing? <b>+</b></div>
  <div class="faq-item" style="left:163px;top:341px">How long does it take to get started? <b>+</b></div>
  <div class="faq-item" style="left:622px;top:157px">Do I have to sign a contract? <b>+</b></div>
  <div class="faq-item" style="left:622px;top:205px">Do I have to purchase any hardware or equipment? <b>+</b></div>
  <div class="faq-item" style="left:622px;top:253px">I'm not sure how many minutes I'll need? <b>+</b></div>
  <div class="faq-item" style="left:622px;top:301px">Can I change my service plan? <b>+</b></div>

  <h2 class="abs cta-text">READY TO TAKE YOUR BUSINESS<br>TO THE NEXT LEVEL</h2>
  <div class="abs cta-btn">GET STARTED</div>
  <div class="abs art" role="img" aria-label="Large rocket illustration lifting off from clouds" style="left:985px;top:520px;width:120px;height:265px;border-radius:60px 60px 0 0;background:linear-gradient(180deg,#9fe2cd,#6dcfb2)"></div>
</section>

<!-- Contact -->
<section class="band mint" style="top:4000px;height:341px">
  <div class="abs contact-card">
    <h3>Contact Details</h3>
    <div class="contact-row"><svg><use href="#i-phone"/></svg>Phone: (808) 555-0142</div>
    <div class="contact-row"><svg><use href="#i-mail"/></svg>hello@loftwell.co</div>
    <div class="contact-row"><svg><use href="#i-pin"/></svg>Loftwell Inc,<br>410 Harbor Rd, Fresno, CA 93711</div>
  </div>
  <h2 class="abs form-title">Request For Call Back</h2>
  <div class="field" style="left:489px;top:140px">Name</div>
  <div class="field" style="left:758px;top:140px">Email</div>
  <div class="field" style="left:489px;top:192px">Ph Num</div>
  <div class="field" style="left:758px;top:192px">Enquiry About</div>
  <div class="abs submit">Submit Now</div>
</section>

<!-- Footer -->
<footer class="band plain" style="top:4341px;height:103px">
  <p class="abs copy">Copyright © 2018<br>All rights reserved</p>
  <nav class="abs foot-nav"><a class="active">Home</a><a>About Us</a><a>Service</a><a>Pricing</a><a>Contact Us</a><a>Account</a></nav>
  <div class="abs socials"><span></span><span></span><span></span><span></span></div>
</footer>

</body>
</html>
```